Card Design Project

We are looking for a couple card / box designs that will for a new company that is in the bereavement assistance industry.
Our customers are churches, counseling centers and funeral homes.
Once we have these card designs we will need to work with that same artist to help us out with box graphic designs that are similar to the card designs. The box is 12" long x 4" wide x 6" high
We will need more designs in the future so we are looking for an artist for future work.
Our look needs to be professional and solemn.
The front of the card should be quite close to what i am attaching but with some professional touches to it that give it a proper look. We dont want you to stray to far from what i have attached but if you feel you have some good ideas we would be more than happy to see them.
The back of the card we want people to be able to leave the family a note so will need wording such as "leave a message to the family" or "write a memory"
Keep in mind we will need this look to be able to match graphics on the box as well, we kind of need the card design and box design to go together.
Thanks
Just wanted to mention to all designers that although we would like our logo on the card it is something that we need to keep kind of in the background somehow. We cant be seen as trying to push a brand name too much so please keep that in mind. Thanks
Designers, I took the need to see what the design looked like on a box out.
Target Market(s)
Funeral homes, churches, counseling centers
Industry/Entity Type
Industry
Requirements
Must have
- Professional and solemn look
Card need to be 4"wide X 6" high and needs to be portrait
A pin will be attached to the top right part of the card so will need a space there for it.
I was thinking that we would have the pic of the ribbon symbol there so when the pin is off the card there would still be a ribbon pic there. The pins that we will be attaching are ribbon pins similar to what i have on my pdf's
Please keep in mind that we cant really have out logo in a dominant area on the card. We would like to have it subtly in there but not to where it is in your face type of thing.
Nice to have
- Our logo but very small, not to intrusive .
Would like 2 designs, one dark and another light.
Maybe 1 masculine or gender neutral and another feminine
Wording should be the same

```html
<!DOCTYPE html>
<html lang="en">
<head>
<meta charset="utf-8">
<title>Sympathy Card – Light and Dark</title>
<link rel="stylesheet" href="https://fonts.googleapis.com/css2?family=Open+Sans:ital,wght@0,300;0,400;0,600;1,300;1,400&display=swap">
<style>
  :root {
    --page: #ffffff;
    --frame: #9c9c9c;
    --ink: #2b2b2b;
    --ink-soft: #3a3a3a;
    --paper-dark: #000000;
    --ink-light: #f2f2f2;
    --mark-light: #b5b5b5;
    --mark-dark: #8a8a8a;
    --blossom: #e2b9c8;
    --blossom-deep: #b07088;
    --ghost: #e4e4e4;
  }
  * { margin: 0; padding: 0; box-sizing: border-box; }
  html, body {
    width: 795px; height: 1200px; overflow: hidden;
    background: var(--page);
    font-family: "Open Sans", Arial, sans-serif;
  }
  .sheet { position: relative; width: 795px; height: 1200px; }

  .card {
    position: absolute; left: 22px; width: 754px; height: 566px;
    border: 1px solid var(--frame);
    display: flex; overflow: hidden;
  }
  .card--light { top: 22px; }
  .card--dark { top: 613px; }

  .card__front, .card__back { position: relative; height: 100%; }
  .card__front { width: 377px; }
  .card__back { flex: 1; border-left: 1px solid var(--frame); background: var(--page); }
  .card--dark .card__front { background: var(--paper-dark); }

  .pin-mark {
    position: absolute; left: 270px; top: 19px; width: 88px;
    display: flex; flex-direction: column; align-items: center;
  }
  .pin-mark__spot { width: 84px; height: 79px; background: var(--mark-light); }
  .card--dark .pin-mark__spot { background: var(--mark-dark); }
  .pin-mark__name {
    margin-top: 6px; font-weight: 600; font-size: 15px; line-height: 17px;
    text-align: center; color: var(--ink); white-space: nowrap;
  }
  .card--dark .pin-mark__name { color: var(--ink-light); }

  .greeting {
    position: absolute; left: 44px; top: 111px;
    font-weight: 300; font-style: italic; font-size: 32px; line-height: 30px;
    color: var(--ink);
  }
  .message {
    position: absolute; left: 43px; top: 203px;
    font-weight: 300; font-size: 12.2px; line-height: 15.9px; color: var(--ink-soft);
    white-space: nowrap;
  }
  .message p { margin-bottom: 15.9px; }
  .message .thanks { position: absolute; top: 267px; left: 0; }
  .card--dark .greeting, .card--dark .message { color: var(--ink-light); }

  .photo { position: absolute; }
  .photo--blossom {
    left: 212px; top: 236px; width: 165px; height: 330px;
    background: radial-gradient(ellipse 50% 52% at 55% 48%, var(--blossom) 0%, var(--blossom-deep) 50%, rgba(255,255,255,0) 100%);
  }
  .photo--blossom-ghost {
    left: 0; top: 215px; width: 180px; height: 330px;
    background: radial-gradient(ellipse 55% 50% at 35% 45%, var(--ghost) 0%, rgba(255,255,255,0) 100%);
  }
  .photo--fabric {
    left: 150px; top: 90px; width: 227px; height: 476px;
    background: radial-gradient(ellipse 85% 75% at 95% 80%, #444444 0%, #222222 45%, rgba(0,0,0,0) 100%);
  }
  .photo--fabric-ghost {
    left: 0; top: 110px; width: 260px; height: 456px;
    background: radial-gradient(ellipse 70% 60% at 10% 55%, var(--ghost) 0%, rgba(255,255,255,0) 100%);
  }

  .prompt {
    position: absolute; left: 0; right: 0; top: 80px;
    text-align: center; padding-left: 8px;
    font-weight: 300; font-style: italic; font-size: 20px; color: var(--ink);
  }
</style>
</head>
<body>
<main class="sheet">

  <section class="card card--light">
    <div class="card__front">
      <div class="photo photo--blossom" role="img" aria-label="Photograph of a pink cherry blossom branch"></div>
      <div class="pin-mark">
        <div class="pin-mark__spot" role="img" aria-label="Space where the ribbon pin is attached"></div>
        <div class="pin-mark__name">SHARING<br>SORROW</div>
      </div>
      <h1 class="greeting">Dear<br>Friends</h1>
      <div class="message">
        <p>Your support in attending<br>this memorial and celebration<br>of life means so much to us.</p>
        <p>Our loved one has touched<br>you in ways we may not<br>even recognize yet.</p>
        <p>We invite you to wear this<br>pin through your grieving<br>process, which we receive as<br>a symbol of your sympathy<br>and support of our loss</p>
        <p class="thanks">Thank you for grieving<br>together with us</p>
      </div>
    </div>
    <div class="card__back">
      <div class="photo photo--blossom-ghost" role="img" aria-label="Faded grey mirror image of the cherry blossom branch"></div>
      <p class="prompt">write a memory</p>
    </div>
  </section>

  <section class="card card--dark">
    <div class="card__front">
      <div class="photo photo--fabric" role="img" aria-label="Close-up photograph of dark woven fabric texture"></div>
      <div class="pin-mark">
        <div class="pin-mark__spot" role="img" aria-label="Space where the ribbon pin is attached"></div>
        <div class="pin-mark__name">SHARING<br>SORROW</div>
      </div>
      <h1 class="greeting">Dear<br>Friends</h1>
      <div class="message">
        <p>Your support in attending<br>this memorial and celebration<br>of life means so much to us.</p>
        <p>Our loved one has touched<br>you in ways we may not<br>even recognize yet.</p>
        <p>We invite you to wear this<br>pin through your grieving<br>process, which we receive as<br>a symbol of your sympathy<br>and support of our loss</p>
        <p class="thanks">Thank you for grieving<br>together with us</p>
      </div>
    </div>
    <div class="card__back">
      <div class="photo photo--fabric-ghost" role="img" aria-label="Faded light grey woven fabric texture"></div>
      <p class="prompt">write a memory</p>
    </div>
  </section>

</main>
</body>
</html>
```